Vehicle Rental Hire in the Algarve - Portugal

We are opening a Vehicle Rental company in the Algarve - Portugal - this will attract both locals and Tourists visiting. So we want this website to capture the beautiful location we will be set in, along with the familiarity of a vehicle rental company. And to keep a colour scheme in Line with out Logo. We are Quenmira Vehicle Rental.

Industry/Entity Type

Vehicle Rental

Number of Pages Required

1 page

Requirements
Must have
• must be professional, and simple to use navigation bar - must also have a "make a reservation" box - similar to the screenshot attached - Under our logo it must read "Vehicle Rental"
Nice to have
• It needs to be in a colour scheme that fits in with our logo

```html
<!DOCTYPE html>
<html lang="en">
<head>
<meta charset="utf-8">
<title>Quenmira Vehicle Rental</title>
<link href="https://fonts.googleapis.com/css2?family=Poppins:wght@400;500;600;700&family=Questrial&display=swap" rel="stylesheet">
<style>
:root{
  --blue:#1b0fdc;
  --red:#c2302b;
  --dark:#161616;
  --ink:#222;
  --muted:#777;
  --white:#fff;
  --tint:#ecebfd;
}
*{box-sizing:border-box;margin:0;padding:0}
html,body{width:1200px;height:4277px;overflow:hidden}
body{position:relative;font-family:'Poppins',sans-serif;color:var(--ink);background:var(--white)}
.abs{position:absolute}
.topbar{left:0;top:0;width:1200px;height:40px;background:var(--blue);color:#fff;font-size:12px;z-index:4}
.topbar .login{left:143px;top:11px;display:flex;gap:7px;align-items:center}
.topbar .lang{left:990px;top:9px;display:flex;gap:6px;align-items:center}
.flag{width:22px;height:22px;border-radius:50%;background:#d9262b;border:2px solid #fff}
.nav{left:0;top:40px;width:1200px;height:61px;background:#fff;box-shadow:0 2px 6px rgba(0,0,0,.08);z-index:2}
.nav a{position:absolute;top:24px;font-size:13px;color:#333;text-decoration:none;letter-spacing:.2px}
.nav a.active{color:var(--red)}
.nav a.active::before{content:"";position:absolute;left:-2px;right:-2px;top:-24px;height:4px;background:var(--red)}
.logo{left:132px;top:38px;width:170px;height:152px;border-radius:0 0 85px 85px;background:#fff;box-shadow:0 6px 12px rgba(0,0,0,.12);z-index:3;display:flex;flex-direction:column;align-items:center;justify-content:center;color:var(--blue);font-family:'Questrial',sans-serif;font-size:21px;line-height:1.2;text-align:center}
.hero{left:0;top:101px;width:1200px;height:601px;background:linear-gradient(180deg,#e9a55c 0%,#f1c37c 18%,#6a86a1 40%,#2f5566 62%,#6b5a3b 82%,#4d6a2c 100%)}
.band{left:0;top:702px;width:1200px;height:175px;background:var(--red)}
.car{left:118px;top:465px;width:540px;height:295px;border-radius:10px;background:linear-gradient(180deg,rgba(255,255,255,.92),rgba(205,208,212,.92));box-shadow:0 8px 20px rgba(0,0,0,.18)}
.support{left:0;top:795px;width:1200px;text-align:center;color:#fff;font-size:25px;display:flex;justify-content:center;align-items:center;gap:12px}
.support b{font-weight:600}
.reserve{left:672px;top:207px;width:384px;height:538px;background:var(--blue);color:#fff;padding:0 30px}
.reserve h2{font-family:'Poppins',sans-serif;font-weight:500;font-size:19px;text-align:center;margin-top:22px;padding-bottom:12px;border-bottom:1px solid rgba(255,255,255,.35)}
.reserve .lbl{position:absolute;font-size:11.5px}
.field{position:absolute;height:35px;background:#fff;border-radius:18px;color:#888;font-size:11.5px;padding:0 16px;display:flex;align-items:center;justify-content:space-between}
.field i{font-style:normal;color:var(--blue);font-size:9px}
.check{position:absolute;font-size:11.5px;display:flex;gap:8px;align-items:center}
.btn-red{position:absolute;background:var(--red);color:#fff;border-radius:18px;font-size:11px;font-weight:600;display:flex;align-items:center;justify-content:center}
.rule{position:absolute;left:553px;width:94px;height:2px;background:var(--red)}
.title{position:absolute;left:0;width:1200px;text-align:center;font-family:'Questrial',sans-serif;font-weight:400;font-size:36px;color:var(--ink)}
.step{position:absolute;width:260px;text-align:center}
.step .box{width:110px;height:110px;margin:0 auto;border-radius:6px;background:var(--tint);display:flex;align-items:center;justify-content:center}
.step .box.on{background:var(--blue)}
.step h3{font-size:16px;font-weight:600;margin-top:22px}
.step p{font-size:11.5px;color:var(--muted);line-height:20px;margin-top:10px}
.about{left:0;top:1378px;width:1200px;height:576px;background:var(--blue);color:#fff}
.about .frame{left:108px;top:70px;width:166px;height:229px;border:2px solid #fff;border-right:none;border-radius:30px 0 0 30px}
.about .photo{left:144px;top:104px;width:354px;height:369px;background:linear-gradient(160deg,#b9c3c4,#5f7a5a 55%,#9a9a8a)}
.about .carimg{left:238px;top:272px;width:358px;height:176px;border-radius:10px;background:linear-gradient(180deg,#d3343c,#8c141b);box-shadow:0 8px 18px rgba(0,0,0,.25)}
.about .line{left:631px;top:104px;width:92px;height:2px;background:#fff}
.about h2{position:absolute;left:631px;top:120px;font-family:'Questrial',sans-serif;font-weight:400;font-size:36px}
.about p{position:absolute;left:631px;top:176px;width:425px;font-size:12.6px;line-height:20px;text-align:justify}
.loc{position:absolute;width:432px;height:375px}
.loc .lab{position:absolute;left:68px;top:343px;width:294px;height:65px;background:#fff;box-shadow:0 4px 12px rgba(0,0,0,.12);display:flex;align-items:center;justify-content:center;font-weight:600;font-size:18px}
.services{left:0;top:2653px;width:1200px;height:561px;background:var(--red);color:#fff}
.svc{position:absolute;width:210px;text-align:center}
.svc .ring{width:210px;height:210px;border-radius:50%;border:3px solid #fff;padding:6px}
.svc .ring div{width:100%;height:100%;border-radius:50%}
.svc span{display:block;margin-top:16px;font-size:15px;font-weight:500}
.card{position:absolute;width:281px;height:415px;background:#fff;box-shadow:0 3px 14px rgba(0,0,0,.1);padding:10px 14px}
.card .img{width:254px;height:195px}
.card .date{margin-top:22px;font-size:11.5px;color:var(--red);display:flex;gap:6px;align-items:center}
.card h4{font-size:15px;font-weight:600;line-height:24px;margin-top:10px}
.card p{font-size:11.5px;color:var(--muted);line-height:20px;margin-top:6px}
.card a{display:block;margin-top:12px;font-size:15px;font-weight:700;color:var(--blue);text-decoration:underline}
.footer{left:0;top:3914px;width:1200px;height:363px;background:var(--dark);color:#fff}
.footer h5{position:absolute;top:82px;font-size:19px;font-weight:600}
.footer p,.footer li{font-size:12.6px;line-height:20px}
.footer ul{list-style:none}
.footer li{display:flex;gap:14px}
.footer .dots{left:108px;top:276px;width:983px;border-top:2px dotted #bbb}
.footer .copy{left:0;top:308px;width:1200px;text-align:center;font-size:12px}
</style>
</head>
<body>

<div class="abs topbar">
  <div class="abs login"><svg width="10" height="11" viewBox="0 0 10 11"><circle cx="5" cy="3" r="2.6" fill="#fff"/><path d="M0 11c0-3.5 2-5 5-5s5 1.5 5 5z" fill="#fff"/></svg>Partner Login</div>
  <div class="abs lang"><div class="flag"></div>Eng ▾</div>
</div>

<nav class="abs nav">
  <a class="active" style="left:390px">HOME</a>
  <a style="left:458px">FLEET</a>
  <a style="left:521px">PROMOTIONS</a>
  <a style="left:637px">EXTRAS &amp; SERVICES</a>
  <a style="left:793px">ABOUT US</a>
  <a style="left:888px">PARTNERS</a>
  <a style="left:983px">CONTACTS</a>
</nav>

<div class="abs logo">QUENMIRA<br>Vehicle Rental</div>

<div class="abs hero" role="img" aria-label="Algarve coastline at sunset with sea stacks and cliffs"></div>
<div class="abs band"></div>
<div class="abs car" role="img" aria-label="White SUV rental car"></div>

<div class="abs support">
  <svg width="30" height="30" viewBox="0 0 24 24"><path d="M6.6 10.8a15 15 0 0 0 6.6 6.6l2.2-2.2c.3-.3.7-.4 1-.2 1.1.4 2.3.6 3.6.6.6 0 1 .4 1 1V20c0 .6-.4 1-1 1A17 17 0 0 1 3 4c0-.6.4-1 1-1h3.5c.6 0 1 .4 1 1 0 1.2.2 2.4.6 3.6.1.3 0 .7-.2 1z" fill="#fff"/><path d="M14 3a7 7 0 0 1 7 7M14 6a4 4 0 0 1 4 4" stroke="#fff" stroke-width="1.6" fill="none"/></svg>
  <span>Customer Support - <b>+1 888 888 8888</b></span>
</div>

<form class="abs reserve">
  <h2>MAKE A RESERVATION</h2>
  <span class="lbl" style="top:70px">Pick up location</span>
  <div class="field" style="left:32px;top:93px;width:322px">Please choose.. <i>▼</i></div>
  <div class="check" style="left:32px;top:142px"><svg width="11" height="11" viewBox="0 0 11 11"><rect x=".5" y=".5" width="10" height="10" fill="none" stroke="#fff"/><path d="M2.5 5.5l2 2 4-4" stroke="#fff" stroke-width="1.5" fill="none"/></svg>Pick up location same as return location</div>
  <span class="lbl" style="top:173px">Driver's age</span>
  <div class="field" style="left:32px;top:198px;width:322px">Please choose.. <i>▼</i></div>
  <span class="lbl" style="top:246px">Vehicle category</span>
  <div class="field" style="left:32px;top:269px;width:322px">All <i>▼</i></div>
  <span class="lbl" style="top:318px">Pick up date</span>
  <span class="lbl" style="left:199px;top:318px">Hour</span>
  <div class="field" style="left:32px;top:341px;width:153px">dd-mm-yy <i>▦</i></div>
  <div class="field" style="left:199px;top:341px;width:155px">9.00 <i>◎</i></div>
  <span class="lbl" style="top:389px">Drop off date</span>
  <span class="lbl" style="left:199px;top:389px">Hour</span>
  <div class="field" style="left:32px;top:412px;width:153px">dd-mm-yy <i>▦</i></div>
  <div class="field" style="left:199px;top:412px;width:155px">9.00 <i>◎</i></div>
  <div class="btn-red" style="left:32px;top:470px;width:322px;height:34px">SEARCH NOW</div>
</form>

<section>
  <div class="rule" style="top:957px"></div>
  <h2 class="title" style="top:970px">HOW IT WORKS</h2>
  <svg class="abs" style="left:370px;top:1075px" width="160" height="50" viewBox="0 0 160 50"><path d="M5 45C40 0 110 0 150 42" stroke="#555" stroke-width="1.5" stroke-dasharray="5 5" fill="none"/><path d="M144 36l7 8-10 0" fill="#555"/></svg>
  <svg class="abs" style="left:672px;top:1075px" width="160" height="50" viewBox="0 0 160 50"><path d="M5 45C40 0 110 0 150 42" stroke="#555" stroke-width="1.5" stroke-dasharray="5 5" fill="none"/><path d="M144 36l7 8-10 0" fill="#555"/></svg>
  <div class="step" style="left:165px;top:1062px">
    <div class="box"><svg width="34" height="44" viewBox="0 0 24 32"><path d="M12 0C5.4 0 0 5.4 0 12c0 9 12 20 12 20s12-11 12-20C24 5.4 18.6 0 12 0z" fill="#1b0fdc"/><circle cx="12" cy="12" r="5" fill="#ecebfd"/></svg></div>
    <h3>Choose a location</h3>
    <p>Lorem ipsum dolor sit amet, consectetur adipiscing elit, sed do eiusmod tempor incididunt ut labore</p>
  </div>
  <div class="step" style="left:470px;top:1062px">
    <div class="box on"><svg width="48" height="48" viewBox="0 0 24 24"><rect x="2" y="4" width="20" height="18" rx="2" fill="#fff"/><rect x="6" y="2" width="2" height="4" fill="#fff"/><rect x="16" y="2" width="2" height="4" fill="#fff"/><g fill="#1b0fdc"><rect x="5" y="10" width="3" height="3"/><rect x="10.5" y="10" width="3" height="3"/><rect x="16" y="10" width="3" height="3"/><rect x="5" y="15" width="3" height="3"/><rect x="10.5" y="15" width="3" height="3"/><rect x="16" y="15" width="3" height="3"/></g></svg></div>
    <h3>Pick-up date</h3>
    <p>Lorem ipsum dolor sit amet, consectetur adipiscing elit, sed do eiusmod tempor incididunt ut labore</p>
  </div>
  <div class="step" style="left:773px;top:1062px">
    <div class="box"><svg width="56" height="40" viewBox="0 0 28 20"><path d="M5 8l3-6h12l3 6h2v8h-3v3h-3v-3H9v3H6v-3H3V8z" fill="#1b0fdc"/><rect x="9" y="4" width="10" height="4" fill="#ecebfd"/><circle cx="7" cy="12" r="1.6" fill="#ecebfd"/><circle cx="21" cy="12" r="1.6" fill="#ecebfd"/></svg></div>
    <h3>Book your car</h3>
    <p>Lorem ipsum dolor sit amet, consectetur adipiscing elit, sed do eiusmod tempor incididunt ut labore</p>
  </div>
</section>

<section class="abs about">
  <div class="abs frame"></div>
  <div class="abs photo" role="img" aria-label="Mountain road with limestone cliffs and pine trees"></div>
  <div class="abs carimg" role="img" aria-label="Red sedan rental car"></div>
  <div class="abs line"></div>
  <h2>ABOUT US</h2>
  <p>Lorem ipsum dolor sit amet, consectetur adipiscing elit, sed do eiusmod tempor incididunt ut labore et dolore magna aliqua. Ut enim ad minim veniam, quis nostrud exercitation ullamco laboris nisi ut aliquip ex ea commodo consequat. Duis aute irure dolor in reprehenderit in voluptate velit esse cillum dolore eu fugiat nulla pariatur. Excepteur sint occaecat cupidatat non proident, sunt in culpa qui officia deserunt mollit anim id est laborum. Lorem ipsum dolor sit amet, consectetur adipiscing elit, sed do eiusmod tempor incididunt ut labore et dolore magna aliqua. Ut enim ad minim veniam, quis nostrud exercitation ullamco laboris nisi ut aliquip ex ea commodo consequat. Duis aute irure dolor in reprehenderit</p>
  <div class="btn-red" style="left:631px;top:437px;width:130px;height:35px">LEARN MORE</div>
</section>

<section>
  <div class="rule" style="top:2044px"></div>
  <h2 class="title" style="top:2057px">OUR LOCATIONS</h2>
  <div class="loc" style="left:144px;top:2125px">
    <div style="width:432px;height:375px;background:linear-gradient(180deg,#6fa6d8 0%,#cfe2ee 28%,#c79a62 45%,#2fc0c0 62%,#d9b88a 78%,#c0509a 100%)" role="img" aria-label="Algarve beach with turquoise water, rock formations and pink flowers"></div>
    <div class="lab">ALGARVE</div>
  </div>
  <div class="loc" style="left:624px;top:2125px">
    <div style="width:432px;height:375px;background:linear-gradient(180deg,#5d8fd0 0%,#a9c4e4 25%,#b08f70 45%,#e2c04a 62%,#6f7280 85%,#4c5058 100%)" role="img" aria-label="Colourful Portuguese palace on a hilltop"></div>
    <div class="lab">PORTUGAL</div>
  </div>
</section>

<section class="abs services">
  <div class="abs" style="left:553px;top:96px;width:94px;height:2px;background:#fff"></div>
  <h2 class="title" style="top:109px;color:#fff">OUR SERVICES</h2>
  <div class="svc" style="left:134px;top:192px"><div class="ring"><div style="background:linear-gradient(180deg,#8fb4d8,#e8eef3 40%,#5b6a4c 70%,#3b3b3b)" role="img" aria-label="Car on a mountain road"></div></div><span>Lorem ipsum dolor</span></div>
  <div class="svc" style="left:375px;top:192px"><div class="ring"><div style="background:linear-gradient(180deg,#4f8ed2,#e9d9b5 55%,#2a3fa8 80%)" role="img" aria-label="Traveller sitting on a car roof at the coast"></div></div><span>Lorem ipsum dolor</span></div>
  <div class="svc" style="left:614px;top:192px"><div class="ring"><div style="background:linear-gradient(180deg,#d7dde0,#9aa3a8 50%,#c9c2b6)" role="img" aria-label="Friends standing beside a rental car"></div></div><span>Lorem ipsum dolor</span></div>
  <div class="svc" style="left:855px;top:192px"><div class="ring"><div style="background:linear-gradient(180deg,#3a3a3a,#e8dcc6 50%,#d6c4a4)" role="img" aria-label="Couple relaxing in the open boot of a car at the beach"></div></div><span>Lorem ipsum dolor</span></div>
</section>

<section>
  <h2 class="title" style="top:3314px">LATEST BLOG</h2>
  <svg class="abs" style="left:52px;top:3592px" width="18" height="28" viewBox="0 0 18 28"><path d="M15 2L3 14l12 12" stroke="#222" stroke-width="3" fill="none"/></svg>
  <svg class="abs" style="left:1118px;top:3592px" width="18" height="28" viewBox="0 0 18 28"><path d="M3 2l12 12L3 26" stroke="#222" stroke-width="3" fill="none"/></svg>
  <article class="card" style="left:144px;top:3386px">
    <div class="img" style="background:linear-gradient(180deg,#7fb3e0,#e9c14a 55%,#d8cdb8)" role="img" aria-label="Family sitting in the boot of a car at the beach"></div>
    <div class="date">▦ Jan 20,2024</div>
    <h4>Lorem ipsum dolor sit amet, consectetur</h4>
    <p>Lorem ipsum dolor sit amet, conse ct etur adipiscing elit, sed do eiusmod tempor incididunt ut labore</p>
    <a>Read More ➔</a>
  </article>
  <article class="card" style="left:460px;top:3386px">
    <div class="img" style="background:linear-gradient(180deg,#b8c4c8,#6f7f70 50%,#3a3a36)" role="img" aria-label="Woman leaning on a car door in the mountains"></div>
    <div class="date">▦ Jan 20,2024</div>
    <h4>Lorem ipsum dolor sit amet, consectetur</h4>
    <p>Lorem ipsum dolor sit amet, conse ct etur adipiscing elit, sed do eiusmod tempor incididunt ut labore</p>
    <a>Read More ➔</a>
  </article>
  <article class="card" style="left:774px;top:3386px">
    <div class="img" style="background:linear-gradient(180deg,#d5dde3,#b79d86 45%,#6d7d8a 75%,#bfc3c6)" role="img" aria-label="Car parked above a historic riverside city"></div>
    <div class="date">▦ Jan 20,2024</div>
    <h4>Lorem ipsum dolor sit amet, consectetur</h4>
    <p>Lorem ipsum dolor sit amet, conse ct etur adipiscing elit, sed do eiusmod tempor incididunt ut labore</p>
    <a>Read More ➔</a>
  </article>
</section>

<footer class="abs footer">
  <h5 style="left:143px">About Us</h5>
  <p class="abs" style="left:143px;top:127px;width:270px">Lorem ipsum dolor sit amet, consec tetur adipiscing elit, sed do eiusmod tempor incididunt ut labore et dolore magna aliqua.</p>
  <h5 style="left:486px">Contact Us</h5>
  <ul class="abs" style="left:486px;top:127px;width:260px">
    <li><span style="color:var(--red)">⬤</span><span>123, Lorem ipsum dolor sit amet, consec tetur adip</span></li>
    <li><span style="color:var(--red)">✆</span><span>+1 888 888 8888</span></li>
    <li><span style="color:var(--red)">✉</span><span>info@companyname.com</span></li>
  </ul>
  <h5 style="left:807px">Newsletter</h5>
  <div class="abs" style="left:807px;top:125px;width:249px;height:38px;border-radius:19px;background:#fff;color:#888;font-size:11.5px;padding:11px 20px">Email address</div>
  <div class="btn-red" style="left:807px;top:175px;width:121px;height:37px">SUBSCRIBE</div>
  <div class="abs dots"></div>
  <div class="abs copy">© 2024. Company name &nbsp;|&nbsp; All rights reserved</div>
</footer>

</body>
</html>
```